Buch-/eBook-Cover zum Thema Magersucht
Zielgruppe
Ich bin Autorin und suche ein passendes Buchcover. Die Zielgruppe für dieses Buch sind Eltern von magersüchtigen Kindern sowie interessierte medizinische und therapeutische Fachkräfte.
Aufgabenstellung
Bei meinem Buch handelt es sich um einen Ratgeber zur Behandlung von Magersucht bei Kindern und Jugendlichen.
Folgendes muss auf die Vorderseite des Buches:
Titel: Teller trägt Trost
Untertitel: Elterngestützte Begleitung im Alltag
Helga Brunsmeier
Ich wünsche mir ein einfühlsames Cover, das die Schwere der Krankheit spiegelt, aber auch die Hoffnung auf Heilung. Bitte keine plumpen Bilder von Waage, Massband oder dünnen Körpern.
Der Klappentext im Word-Dokument ist für die Rückseite des Buchcovers.

```html
<!DOCTYPE html>
<html lang="de">
<head>
<meta charset="utf-8">
<title>Teller trägt Trost – Buchcover</title>
<link href="https://fonts.googleapis.com/css2?family=Caveat+Brush&family=Comic+Neue:wght@700&family=Fira+Sans:wght@500&display=swap" rel="stylesheet">
<style>
  :root {
    --page-bg: #eeeeee;
    --sky-top: #9cc2d6;
    --sky-mid: #c9e2e6;
    --sky-low: #8cc3d3;
    --sky-bottom: #5f9cb8;
    --ink-navy: #344a72;
    --figure-dark: #2f4a5a;
    --figure-mid: #4f7d86;
    --figure-light: #b9a58a;
    --subtitle: #ffffff;
  }
  * { margin: 0; padding: 0; box-sizing: border-box; }
  html, body { width: 1200px; height: 958px; overflow: hidden; background: var(--page-bg); }
  .cover {
    position: absolute;
    left: 318px; top: 56px;
    width: 563px; height: 845px;
    overflow: hidden;
    background:
      radial-gradient(ellipse 70% 40% at 50% 35%, rgba(230,244,243,0.9), rgba(230,244,243,0) 70%),
      radial-gradient(ellipse 40% 30% at 85% 70%, rgba(170,225,215,0.6), rgba(170,225,215,0) 70%),
      linear-gradient(180deg, var(--sky-top) 0%, var(--sky-mid) 30%, var(--sky-mid) 55%, var(--sky-low) 82%, var(--sky-bottom) 100%);
  }
  .author {
    position: absolute; top: 84px; left: 0; width: 100%;
    text-align: center;
    font-family: "Comic Neue", cursive;
    font-weight: 700; font-size: 27px; letter-spacing: 1px;
    color: var(--ink-navy);
  }
  .title {
    position: absolute; left: 0; width: 100%;
    text-align: center;
    font-family: "Caveat Brush", cursive;
    color: var(--ink-navy);
    text-transform: uppercase;
    line-height: 1;
  }
  .title-line { display: block; }
  .title-line--big { font-size: 112px; }
  .title-line--small { font-size: 64px; margin: 6px 0 4px; }
  .title { top: 142px; }
  .figure-art {
    position: absolute;
    left: 160px; top: 384px;
    width: 200px; height: 461px;
    border-radius: 45% 45% 20% 20% / 20% 20% 10% 10%;
    background:
      radial-gradient(ellipse 50% 25% at 55% 18%, rgba(47,74,90,0.85), rgba(47,74,90,0) 80%),
      linear-gradient(180deg, rgba(185,165,138,0.35) 0%, var(--figure-mid) 45%, var(--figure-dark) 100%);
    opacity: 0.75;
    filter: blur(6px);
  }
  .subtitle {
    position: absolute; top: 752px; left: 0; width: 100%;
    text-align: center;
    font-family: "Fira Sans", sans-serif;
    font-weight: 500; font-size: 31px; line-height: 44px;
    color: var(--subtitle);
  }
</style>
</head>
<body>
  <main class="cover">
    <p class="author">HELGA BRUNSMEIER</p>
    <div class="figure-art" role="img" aria-label="Aquarell-Illustration: Silhouette eines Mädchens mit langem Haar im sanften Licht"></div>
    <h1 class="title">
      <span class="title-line title-line--big">Teller</span>
      <span class="title-line title-line--small">trägt</span>
      <span class="title-line title-line--big">Trost</span>
    </h1>
    <p class="subtitle">Elterngestützte Begleitung<br>im Alltag</p>
  </main>
</body>
</html>
```